Business Card Design for Occupational Medicine Start Up Company

We need to design a professional business card. We are a healthcare company providing occupational medicine services to blue collar industries. We are professional, efficient and high quality service providers.

Target Market(s)

Blue Collar Industry: Shipbuilding, Ports, Trucking Companies; The Executives and Safety Officers for these companies

Industry/Entity Type

Healthcare

Contact Information for Business Card

Logo, Name, Title, Email, Phone

Other font styles liked:
• Please match our Brand Guide

Requirements
Must have
• Our Company Colors and Logo

```html
<!DOCTYPE html>
<html lang="en">
<head>
<meta charset="utf-8">
<title>Crewline Health — Business Card</title>
<link href="https://fonts.googleapis.com/css2?family=Montserrat:wght@300;400;500;700;800&display=swap" rel="stylesheet">
<style>
  :root {
    --navy: #2b2a7c;
    --navy-deep: #221f6b;
    --sky: #2ea3de;
    --gold: #f2b233;
    --paper: #ffffff;
    --ink: #1f1d55;
    --stage: #e9e9ee;
    --faint-lilac: #e3e2f1;
    --faint-sky: #e4f1fa;
  }
  * { margin: 0; padding: 0; box-sizing: border-box; }
  html, body {
    width: 1200px; height: 1186px; overflow: hidden;
    background: var(--stage);
    font-family: "Montserrat", sans-serif;
  }
  .sheet { position: relative; width: 1200px; height: 1186px; }
  .card {
    position: absolute; left: 160px; width: 880px; height: 503px;
    border-radius: 34px; overflow: hidden;
    box-shadow: 0 10px 30px rgba(20, 20, 50, 0.18);
  }
  .card--back { top: 60px; background: var(--navy); }
  .card--front { top: 623px; background: var(--paper); }

  .back-pattern {
    position: absolute; inset: 0;
    background: linear-gradient(135deg, #2f2d86 0%, #2a2879 50%, #312f8a 100%);
  }
  .back-brand {
    position: absolute; right: 70px; top: 232px;
    display: flex; align-items: center; gap: 10px;
    color: var(--paper); font-weight: 700; font-size: 18px; letter-spacing: 1px;
  }
  .back-brand .dot { width: 14px; height: 14px; border-radius: 50%; background: var(--sky); }

  .front-art { position: absolute; inset: 0; }
  .faint-mark {
    position: absolute; left: 0; top: 40px; width: 300px; height: 260px;
    background: linear-gradient(135deg, var(--faint-sky), var(--faint-lilac) 60%, #fdf3e1);
    opacity: 0.75;
    border-radius: 0 40px 40px 0;
  }

  .brand {
    position: absolute; right: 50px; top: 70px;
    display: flex; align-items: center; gap: 14px;
  }
  .brand .dot { width: 22px; height: 22px; border-radius: 50%; background: var(--sky); }
  .brand-name {
    color: var(--navy); font-weight: 800; font-size: 38px; letter-spacing: 1px; line-height: 1;
  }

  .address {
    position: absolute; right: 60px; top: 268px; text-align: right;
    color: var(--ink); font-size: 17px; line-height: 1.35; font-weight: 400;
  }
  .website {
    position: absolute; right: 50px; bottom: 46px;
    color: var(--paper); font-size: 18px; font-weight: 400; letter-spacing: 0.3px;
  }

  .person { position: absolute; left: 60px; top: 318px; }
  .person-name { color: var(--navy); font-weight: 800; font-size: 32px; line-height: 1.1; }
  .person-title { color: var(--ink); font-size: 18px; font-weight: 400; margin-top: 2px; }
  .person-rule { width: 250px; height: 2px; background: var(--sky); margin: 10px 0 12px; }
  .contact { list-style: none; color: var(--ink); font-size: 18px; }
  .contact li { display: flex; align-items: center; gap: 12px; margin-bottom: 6px; }
  .contact svg { width: 16px; height: 16px; fill: var(--sky); flex: none; }
</style>
</head>
<body>
<main class="sheet">

  <section class="card card--back" aria-label="Card back">
    <div class="back-pattern" role="img" aria-label="Repeating brand pattern in violet tones"></div>
    <div class="back-brand"><span class="dot"></span>CREWLINE HEALTH</div>
  </section>

  <section class="card card--front" aria-label="Card front">
    <div class="faint-mark" role="img" aria-label="Faint large brand decoration"></div>

    <svg class="front-art" viewBox="0 0 880 503" aria-hidden="true">
      <line x1="610" y1="252" x2="830" y2="252" stroke="var(--gold)" stroke-width="2"/>
      <line x1="320" y1="330" x2="610" y2="252" stroke="var(--navy)" stroke-width="2"/>
      <path d="M520 503 L520 440 C540 400 560 360 620 352 L880 340 L880 503 Z" fill="var(--navy)"/>
      <path d="M0 470 L470 470 C500 470 520 440 540 405 L560 390 C530 440 510 485 470 492 L0 492 Z" fill="var(--sky)"/>
      <path d="M0 492 L880 492 L880 503 L0 503 Z" fill="var(--navy-deep)"/>
    </svg>

    <div class="brand">
      <span class="dot"></span>
      <span class="brand-name">CREWLINE HEALTH</span>
    </div>

    <div class="address">410 Harbor View Rd, #112<br>Marlow, OH 43000</div>

    <div class="person">
      <div class="person-name">Daniel Reyes</div>
      <div class="person-title">CEO &amp; Founder</div>
      <div class="person-rule"></div>
      <ul class="contact">
        <li>
          <svg viewBox="0 0 24 24"><path d="M6.6 10.8a15 15 0 0 0 6.6 6.6l2.2-2.2c.3-.3.7-.4 1-.2 1.1.4 2.3.6 3.6.6.6 0 1 .4 1 1V20c0 .6-.4 1-1 1A17 17 0 0 1 3 4c0-.6.4-1 1-1h3.5c.6 0 1 .4 1 1 0 1.3.2 2.5.6 3.6.1.3 0 .7-.2 1z"/></svg>
          800-555-0142
        </li>
        <li>
          <svg viewBox="0 0 24 24"><path d="M2 5h20v14H2z M2 5l10 8 10-8" /></svg>
          info@crewlinehealth.com
        </li>
      </ul>
    </div>

    <div class="website">www.crewlinehealth.com</div>
  </section>

</main>
</body>
</html>
```